Custom hot rod builder needs a website for launch of new business where he will build luxury garages

We need a website that gives a WOW first impression for "Summit Carports". This is a new business so photos are renderings but we need it to really attract a particular audience. Our initial business is custom hot rods so now we are building garages for them. These will be like luxury "homes" for cars! I will attach our new logo. Website needs to feel powerful and prestigious.

Target Market(s)

middle aged men, car enthusiasts

Industry/Entity Type

automotive, construction

Coding

Coded - Design and coding required

Number of Pages Required

2 page

Font styles to use
Serif

Colors
0054AA
0677BA
7BADD7
CADEEF
E8F1F8

Requirements
Must have
• a WOW factor. luxury. contact form.
Nice to have
• ?

```html
<!DOCTYPE html>
<html lang="en">
<head>
<meta charset="utf-8">
<title>Summit Carports</title>
<link href="https://fonts.googleapis.com/css2?family=Dancing+Script:wght@500&family=Montserrat:wght@400;500;600;700&family=Saira:wght@300;400&family=Archivo+Black&display=swap" rel="stylesheet">
<style>
:root{
  --bg:#000000;
  --header:#0a0b14;
  --panel:#111214;
  --blue-deep:#0054AA;
  --blue:#0677BA;
  --blue-soft:#7BADD7;
  --blue-pale:#CADEEF;
  --blue-mist:#E8F1F8;
  --footer:#29a8e0;
  --footer-ink:#0d2f63;
  --ghost:#0c1a3d;
  --line:#0b4f8a;
  --copy-bar:#2b2b2b;
  --white:#ffffff;
  --text:#e9ecf2;
}
*{margin:0;padding:0;box-sizing:border-box}
html,body{width:1200px;height:3544px;overflow:hidden;background:var(--bg)}
body{position:relative;font-family:"Montserrat",sans-serif;color:var(--text)}
.abs{position:absolute}

/* header */
.site-header{position:absolute;left:0;top:0;width:1200px;height:88px;background:var(--header)}
.brand{position:absolute;display:flex;align-items:center;gap:10px;font-family:"Montserrat",sans-serif;font-weight:700;color:var(--white);letter-spacing:1px;text-transform:uppercase}
.brand-dot{width:34px;height:34px;border-radius:50%;background:var(--blue)}
.site-header .brand{left:67px;top:25px;font-size:20px}
.nav{position:absolute;top:38px;left:0;width:100%}
.nav a{position:absolute;font-size:11.5px;font-weight:500;color:var(--white);text-decoration:none;letter-spacing:.3px}

/* bracket button */
.btn{position:absolute;height:38px;padding-left:16px;display:flex;align-items:center;font-size:12.5px;font-weight:700;color:var(--white);letter-spacing:.4px;border-left:2px solid var(--blue)}
.btn::before,.btn::after{content:"";position:absolute;left:0;width:26px;height:2px;background:var(--blue)}
.btn::before{top:0}.btn::after{bottom:0}
.btn .arrow{margin-left:8px;width:40px;height:8px}
.btn.nav-contact{left:873px;top:26px;height:36px;font-weight:500;font-size:12.5px}

/* hero */
.hero{position:absolute;left:0;top:88px;width:1200px;height:500px;background:linear-gradient(180deg,#6b4628 0%,#3f2a1c 35%,#2f4a45 65%,#8c5a2c 100%)}

/* section headings */
.ghost{position:absolute;font-family:"Archivo Black",sans-serif;color:var(--ghost);letter-spacing:4px;text-transform:uppercase;line-height:1}
.script{position:absolute;z-index:2;font-family:"Dancing Script",cursive;font-size:62px;color:var(--white);line-height:1}
.kicker{position:absolute;z-index:2;font-family:"Saira",sans-serif;font-weight:300;font-size:29px;color:var(--white);line-height:1;text-transform:uppercase;white-space:nowrap}
.kicker-rule{position:absolute;left:135px;width:97px;height:1px;background:var(--blue)}
.divider{position:absolute;left:206px;width:785px;height:2px;background:var(--line)}

.photo{position:absolute;z-index:1}
.dots{position:absolute;background-image:radial-gradient(circle,#7d8799 1.2px,transparent 1.5px);background-size:11px 11px}

.about-copy{position:absolute;left:619px;top:1078px;width:380px;font-size:12.6px;line-height:25px;color:var(--text)}

/* services */
.service-card{position:absolute;top:1537px;width:199px;height:281px;background:var(--panel);border-left:1px solid #2a2f38;border-right:1px solid #2a2f38;border-bottom:1px solid var(--line)}
.service-icon{position:absolute;left:64px;top:-34px;width:68px;height:68px;border-radius:50%;background:var(--blue-pale);display:flex;align-items:center;justify-content:center}
.service-icon.active{background:var(--blue-deep)}
.service-title{position:absolute;left:23px;top:43px;font-size:15.5px;font-weight:500;color:var(--white);line-height:19px;text-transform:uppercase}
.service-text{position:absolute;left:23px;top:99px;width:165px;font-size:11.7px;line-height:18.6px;color:var(--text)}
.service-arrow{position:absolute;left:22px;top:248px}

/* contact form */
.form-panel{position:absolute;left:534px;top:2790px;width:470px;height:311px;background:var(--panel);border:1px solid var(--line)}
.field{position:absolute;font-size:11.5px;font-weight:500;color:var(--text);text-transform:uppercase;border-bottom:1px solid var(--blue);padding-bottom:10px}

/* footer */
.site-footer{position:absolute;left:0;top:3186px;width:1200px;height:322px;background:var(--footer)}
.site-footer .brand{left:198px;top:68px;font-size:22px;color:var(--white)}
.site-footer .brand-dot{background:var(--white)}
.foot-heading{position:absolute;font-size:12.5px;font-weight:700;color:var(--footer-ink);text-transform:uppercase;letter-spacing:.3px}
.foot-heading::after{content:"";position:absolute;left:0;top:22px;width:110px;height:1px;background:var(--blue-mist)}
.foot-links{position:absolute;list-style:none}
.foot-links li{font-size:11.5px;font-weight:500;color:var(--footer-ink);height:31px;text-transform:uppercase}
.social{position:absolute;top:3408px;width:30px;height:30px;border-radius:50%}
.copyright{position:absolute;left:0;top:3508px;width:1200px;height:36px;background:var(--copy-bar);font-size:10.5px;letter-spacing:1px;color:#d4d4d4;display:flex;align-items:center;justify-content:center}
</style>
</head>
<body>

<svg width="0" height="0" style="position:absolute">
  <defs>
    <symbol id="arrow" viewBox="0 0 40 8"><line x1="0" y1="4" x2="34" y2="4" stroke="#0677BA" stroke-width="1.2"/><path d="M33 1 L39 4 L33 7 Z" fill="#0677BA"/></symbol>
    <symbol id="car-icon" viewBox="0 0 36 36"><path d="M7 20 L10 12 Q11 10 13 10 H23 Q25 10 26 12 L29 20 V27 H25 V25 H11 V27 H7 Z" fill="currentColor"/><rect x="12" y="13" width="12" height="5" rx="1" fill="#fff" opacity=".85"/><circle cx="11.5" cy="21.5" r="1.6" fill="#fff"/><circle cx="24.5" cy="21.5" r="1.6" fill="#fff"/><path d="M13 6 l1 1.5 M18 4 v2 M23 6 l-1 1.5" stroke="currentColor" stroke-width="1.2"/></symbol>
    <symbol id="circle-arrow" viewBox="0 0 50 22"><circle cx="11" cy="11" r="10" fill="none" stroke="#0677BA" stroke-width="1.2"/><line x1="11" y1="11" x2="44" y2="11" stroke="#0677BA" stroke-width="1.2"/><path d="M43 8 L49 11 L43 14 Z" fill="#0677BA"/></symbol>
  </defs>
</svg>

<header class="site-header">
  <div class="brand"><span class="brand-dot"></span>Summit Carports</div>
  <nav class="nav">
    <a style="left:488px">HOME</a>
    <a style="left:557px">ABOUT US</a>
    <a style="left:651px">SERVICES</a>
    <a style="left:741px">GALLERY</a>
  </nav>
  <div class="btn nav-contact">CONTACT US</div>
</header>

<div class="hero" role="img" aria-label="Rendering of a luxury car garage interior with brick walls, wooden ceiling and classic cars"></div>

<section class="about">
  <div class="ghost" style="left:412px;top:642px;font-size:60px">ABOUT US</div>
  <div class="dots" style="left:940px;top:665px;width:90px;height:85px"></div>
  <div class="script" style="left:210px;top:678px">About</div>
  <div class="kicker-rule" style="top:753px"></div>
  <div class="kicker" style="left:245px;top:740px;letter-spacing:9px">Summit Carports</div>
  <div class="dots" style="left:166px;top:1203px;width:90px;height:90px"></div>
  <div class="photo" style="left:210px;top:800px;width:371px;height:468px;background:linear-gradient(160deg,#6f5a4a,#1a1a1c 55%,#555)" role="img" aria-label="Photo of a classic black vintage luxury car"></div>
  <div class="photo" style="left:619px;top:690px;width:372px;height:357px;background:linear-gradient(180deg,#b8c0c6 0%,#9a2a2a 55%,#707070 100%)" role="img" aria-label="Photo of a restored red vintage van"></div>
  <p class="about-copy">Lorem ipsum dolor sit amet, consectetur adipiscing elit, sed do eiusmod tempor incididunt ut labore et dolore magna aliqua. Quis ipsum suspendisse ultrices gravida. Risus commodo viverra maecenas accumsan lacus vel</p>
  <div class="btn" style="left:619px;top:1198px">READ MORE<svg class="arrow"><use href="#arrow"/></svg></div>
  <div class="divider" style="top:1327px"></div>
</section>

<section class="services">
  <div class="script" style="left:210px;top:1385px">Services</div>
  <div class="kicker-rule" style="top:1461px"></div>
  <div class="kicker" style="left:245px;top:1448px;letter-spacing:30px">Summit Carports</div>

  <article class="service-card" style="left:180px">
    <div class="service-icon" style="color:var(--blue-deep)"><svg width="36" height="36"><use href="#car-icon"/></svg></div>
    <h3 class="service-title">Services<br>Title 1</h3>
    <p class="service-text">Lorem ipsum dolor sit amet, consectetur adipiscing elit, sed do eiusmod tempor incididunt ut labore et dolore magna aliqua. Quis ipsum suspendisse</p>
    <svg class="service-arrow" width="50" height="22"><use href="#circle-arrow"/></svg>
  </article>
  <article class="service-card" style="left:393px">
    <div class="service-icon active" style="color:var(--white)"><svg width="36" height="36"><use href="#car-icon"/></svg></div>
    <h3 class="service-title">Services<br>Title 2</h3>
    <p class="service-text">Lorem ipsum dolor sit amet, consectetur adipiscing elit, sed do eiusmod tempor incididunt ut labore et dolore magna aliqua. Quis ipsum suspendisse</p>
    <svg class="service-arrow" width="50" height="22"><use href="#circle-arrow"/></svg>
  </article>
  <article class="service-card" style="left:606px">
    <div class="service-icon" style="color:var(--blue-deep)"><svg width="36" height="36"><use href="#car-icon"/></svg></div>
    <h3 class="service-title">Services<br>Title 3</h3>
    <p class="service-text">Lorem ipsum dolor sit amet, consectetur adipiscing elit, sed do eiusmod tempor incididunt ut labore et dolore magna aliqua. Quis ipsum suspendisse</p>
    <svg class="service-arrow" width="50" height="22"><use href="#circle-arrow"/></svg>
  </article>
  <article class="service-card" style="left:819px">
    <div class="service-icon" style="color:var(--blue-deep)"><svg width="36" height="36"><use href="#car-icon"/></svg></div>
    <h3 class="service-title">Services<br>Title 4</h3>
    <p class="service-text">Lorem ipsum dolor sit amet, consectetur adipiscing elit, sed do eiusmod tempor incididunt ut labore et dolore magna aliqua. Quis ipsum suspendisse</p>
    <svg class="service-arrow" width="50" height="22"><use href="#circle-arrow"/></svg>
  </article>
</section>

<section class="gallery">
  <div class="script" style="left:210px;top:1905px">Gallery</div>
  <div class="kicker-rule" style="top:1981px"></div>
  <div class="kicker" style="left:245px;top:1968px;letter-spacing:17px">Our Protfolio</div>
  <div class="photo" style="left:0;top:2021px;width:289px;height:428px;background:linear-gradient(180deg,#7b8a5a 0%,#6d7f8a 30%,#b3202a 65%,#2a2a2a 100%)" role="img" aria-label="Photo of a red sports car by the coast"></div>
  <div class="photo" style="left:303px;top:2021px;width:289px;height:206px;background:linear-gradient(180deg,#7a5a48,#d8d4cc 60%,#4a4a4a)" role="img" aria-label="Photo of a white classic saloon"></div>
  <div class="photo" style="left:303px;top:2243px;width:289px;height:206px;background:linear-gradient(180deg,#7a5a48,#1c1c1e 60%,#5a5a5a)" role="img" aria-label="Photo of a black vintage luxury car"></div>
  <div class="photo" style="left:607px;top:2021px;width:289px;height:428px;background:linear-gradient(170deg,#555 0%,#b8452a 40%,#7a2a18 80%,#333 100%)" role="img" aria-label="Photo of an orange vintage car"></div>
  <div class="photo" style="left:911px;top:2021px;width:289px;height:206px;background:linear-gradient(180deg,#a8b0b6,#9a2a2a 60%,#555)" role="img" aria-label="Photo of a red vintage van"></div>
  <div class="photo" style="left:911px;top:2243px;width:289px;height:206px;background:linear-gradient(180deg,#c24a3e 0%,#5a4a6a 50%,#1e1a22 100%)" role="img" aria-label="Photo of a dark hot rod at sunset"></div>
  <div class="btn" style="left:507px;top:2503px">VIEW ALL GALLERY<svg class="arrow"><use href="#arrow"/></svg></div>
  <div class="divider" style="top:2594px"></div>
</section>

<section class="contact">
  <div class="script" style="left:210px;top:2630px">Contact Us</div>
  <div class="kicker-rule" style="top:2709px"></div>
  <div class="kicker" style="left:245px;top:2696px;letter-spacing:14px">Get in touch with us</div>
  <div class="photo" style="left:209px;top:2750px;width:307px;height:376px;background:linear-gradient(170deg,#8a5a3a 0%,#1a2244 45%,#121826 80%,#777 100%)" role="img" aria-label="Photo of a dark blue hot rod with whitewall tyres"></div>
  <div class="ghost" style="left:547px;top:2742px;font-size:58px">LET'S TALK</div>
  <form class="form-panel">
    <div class="field" style="left:17px;top:30px;width:198px">First Name</div>
    <div class="field" style="left:239px;top:30px;width:200px">Last Name</div>
    <div class="field" style="left:17px;top:102px;width:198px">Email</div>
    <div class="field" style="left:239px;top:102px;width:200px">Phone</div>
    <div class="field" style="left:17px;top:170px;width:422px">Message...</div>
    <div class="btn" style="left:151px;top:230px">SUBMIT NOW<svg class="arrow"><use href="#arrow"/></svg></div>
  </form>
</section>

<footer class="site-footer">
  <div class="brand"><span class="brand-dot"></span>Summit Carports</div>
  <div class="foot-heading" style="left:209px;top:169px">Follow us:</div>
  <div class="foot-heading" style="left:520px;top:66px">Quick Links</div>
  <ul class="foot-links" style="left:520px;top:115px">
    <li>Home</li><li>About Us</li><li>Services</li><li>Gallery</li><li>Contact Us</li>
  </ul>
  <div class="abs" style="left:721px;top:76px;width:1px;height:201px;background:var(--footer-ink)"></div>
  <div class="foot-heading" style="left:845px;top:66px">Services</div>
  <ul class="foot-links" style="left:845px;top:115px">
    <li>Services Title 1</li><li>Services Title 2</li><li>Services Title 3</li><li>Services Title 4</li>
  </ul>
</footer>
<div class="social" style="left:208px;background:var(--blue-pale)"></div>
<div class="social" style="left:247px;background:var(--blue-deep)"></div>
<div class="social" style="left:286px;background:var(--blue-pale)"></div>
<div class="copyright">COPYRIGHT © 2022 SUMMIT CARPORTS. ALL RIGHTS RESERVED.</div>

</body>
</html>
```